Accountant website

Please design a accountant website for www.fenwaybridgeadvisory.com.au. This site is majorly out of date, and is not supported by modern browsers.

The style should use the reds from the design at dev.fenwaybridgeadvisory.com.au, and should be modern and make use of Slides (large content slides that the user scrolls through on the front page).

The content is largely already on the site, however happy to move some around to suit the modern design as required.

The dev.fenwaybridgeadvisory.com.au was a rough mock up that I have completed that the client is "happy" with the direction, however this needs a lot of polish and finishing touches, and I will accept designs that differ from this, but highly recommend that this is used as a guide.

Ready to be sliced PSD Only - HTML no required.

In all honesty, although I can technically do a lot of this, the polished finished I want for this site has eluded me in a few attempts, and therefore I am looking out there at you much more artistic people to finish (or redesign if required) this site.

Target Market(s)

Higher end Small - Medium Business

Industry/Entity Type

Accountant

Requirements
Must have
• Must use the logo from dev.fenwaybridgeadvisory.com.au use exactly the red colours as defined in this layout. A basic layout PSD (to get the colour etc) and the logo in ai format is attached to this project. Please ignore the SSL warning on the development site.

The final product does NOT have to be the same as shown on dev.fenwaybridgeadvisory.com.au however the red colour scheme must be used. The client DOES want the logo on the RIGHT.

Must have a front landing page design, and a page layout that considers the other page content (at least one separate PSD)
Nice to have
• I really am looking at a slide format for the front page simular to:

http://www.quillo.com/au/
http://www.vaultmoor.com/

The attached photos should be used on the site. Was considering a rotating banner with these images are a watermark background on a solid Red header bar, but happy to be shown other options.
Should not have
• Please no "Layout Goblin" submissions.

```html
<!DOCTYPE html>
<html lang="en">
<head>
<meta charset="utf-8">
<title>Fenway Bridge Advisory</title>
<link href="https://fonts.googleapis.com/css2?family=Roboto+Condensed:wght@400;700&family=Source+Sans+3:ital,wght@0,400;0,600;0,700;1,400&display=swap" rel="stylesheet">
<style>
:root{
  --red:#9d2a2e;
  --red-dark:#862125;
  --red-text:#a3282d;
  --ink:#222;
  --grey:#6b6b6b;
  --rule:#d8d8d8;
  --paper:#fff;
  --mist:#f1f1f1;
}
*{margin:0;padding:0;box-sizing:border-box}
html,body{width:1110px;height:1200px;overflow:hidden;background:var(--paper)}
body{font-family:"Source Sans 3",Arial,sans-serif;color:var(--grey);position:relative}
.page{position:relative;width:1110px;height:1200px}

/* header */
.topbar{position:absolute;left:0;top:0;width:1110px;height:63px;background:linear-gradient(#fff 60%,#ececec)}
.follow{position:absolute;left:166px;top:26px;display:flex;align-items:center;gap:4px;font-size:7px;letter-spacing:.3px;color:#555}
.follow .label{margin-right:3px}
.social{width:24px;height:24px;border-radius:50%;display:inline-block}
.social.s1{background:#2b6cb3}.social.s2{background:#3cabe0}.social.s3{background:#1f7a9e}.social.s4{background:#e5a324}
.brand{position:absolute;right:170px;top:16px;display:flex;align-items:center;gap:6px}
.brand-name{font-weight:700;font-size:20px;color:var(--ink);letter-spacing:-.2px}
.brand-mark{width:16px;height:16px;background:var(--red)}

/* nav */
.nav{position:absolute;left:0;top:63px;width:1110px;height:34px;background:var(--red);display:flex;padding-left:166px}
.nav a{color:#fff;text-decoration:none;font-weight:700;font-size:10px;text-transform:uppercase;line-height:34px;padding:0 29px}
.nav a.current{background:var(--red-dark);padding:0 36px}

/* hero */
.hero{position:absolute;left:0;top:97px;width:1110px;height:381px;background:linear-gradient(100deg,#c9a980 0%,#b99c78 30%,#6f7d4a 55%,#4f6b36 75%,#8a7257 100%)}
.hero-photo{position:absolute;inset:0}
.hero-copy{position:absolute;left:184px;top:88px;font-family:"Roboto Condensed",Arial,sans-serif;text-transform:uppercase}
.hero-title{color:#fff;font-size:54px;line-height:52px;font-weight:400}
.hero-sub{color:#fff;font-size:40px;line-height:48px}
.hero-tag{color:#1c1c1c;font-size:23px;line-height:34px}
.hero-btn{position:absolute;left:186px;top:242px;width:157px;height:42px;background:var(--red);border-radius:2px;color:#fff;font-family:"Roboto Condensed",Arial,sans-serif;font-size:17px;display:flex;align-items:center;justify-content:center;gap:8px}
.slide-arrow{position:absolute;top:177px;width:32px;height:31px;background:rgba(190,95,80,.55)}
.slide-arrow.prev{left:91px}.slide-arrow.next{left:995px}
.slide-arrow svg{position:absolute;left:12px;top:10px}

/* intro */
.intro-band{position:absolute;left:0;top:478px;width:1110px;height:70px;background:linear-gradient(#e9e9e9,#fff)}
.welcome{position:absolute;left:0;top:508px;width:1110px;text-align:center;color:var(--red-text);font-size:24px}
.intro-text{position:absolute;left:180px;top:548px;width:750px;text-align:center;font-size:10.5px;line-height:17.5px;color:#777}

h2.section{position:absolute;font-weight:400;font-size:21px;color:var(--red-text)}

/* left column */
.team-photo{position:absolute;left:166px;top:659px;width:373px;height:137px;background:linear-gradient(90deg,#b8242c,#c93a40 40%,#a92930 70%,#d9d9d9)}
.diff-text{position:absolute;left:167px;top:815px;width:378px;font-size:8.4px;line-height:14.4px;color:#666}
.diff-text p+p{margin-top:14px}
.btn{position:absolute;background:var(--red);color:#fff;font-size:8.5px;text-transform:uppercase;display:flex;align-items:center;justify-content:center;border-radius:2px}
.testi-nav{position:absolute;left:537px;top:969px}
.testimonial{position:absolute;top:1002px;width:190px}
.testimonial .who{font-size:8.4px;line-height:14.4px;color:var(--red-text);text-transform:uppercase}
.testimonial .quote{margin-top:8px;font-style:italic;font-size:8.3px;line-height:14.4px;color:#777}
.testimonial .more{margin-top:6px;font-size:8.4px;color:var(--red-text)}
.testi-divider{position:absolute;left:364px;top:1003px;width:1px;height:84px;background:var(--rule)}

/* articles */
.article{position:absolute;left:587px;width:343px}
.article .badge{position:absolute;left:0;top:0;width:34px;height:34px;border-radius:50%;background:var(--red)}
.article .badge svg{position:absolute;left:11px;top:11px}
.article h3{position:absolute;left:46px;top:6px;font-weight:400;font-size:12.5px;color:var(--red-text)}
.article .excerpt{position:absolute;left:49px;top:30px;width:290px;font-size:8.3px;line-height:14.4px;color:#666}
.article .comments{position:absolute;left:49px;top:94px;font-size:8px;font-style:italic;color:var(--red-text);display:flex;align-items:center;gap:6px}
.article .rule{position:absolute;left:46px;top:118px;width:297px;height:1px;background:var(--rule)}

/* footer */
.footer{position:absolute;left:0;top:1128px;width:1110px;height:72px;background:var(--red)}
.footer-links{position:absolute;left:168px;top:19px;font-size:7.5px;color:#fff;text-transform:uppercase;white-space:nowrap}
.footer-links span.sep{margin:0 9px}
.copyright{position:absolute;left:168px;top:42px;font-size:7.5px;color:#fff;text-transform:uppercase}
.partner{position:absolute;left:804px;top:13px;display:flex;align-items:center;gap:10px}
.partner .seal{width:44px;height:44px;border-radius:50%;background:#e7f4f5}
.partner .plate{width:78px;height:26px;border-radius:3px;background:rgba(255,255,255,.25)}
</style>
</head>
<body>
<div class="page">

  <header class="topbar">
    <div class="follow"><span class="label">FOLLOW US :</span>
      <span class="social s1"></span><span class="social s2"></span><span class="social s3"></span><span class="social s4"></span>
    </div>
    <div class="brand"><span class="brand-name">FENWAY BRIDGE</span><span class="brand-mark"></span></div>
  </header>

  <nav class="nav">
    <a class="current">About us</a><a>Services</a><a>Working with us</a><a>Testimonials</a><a>News</a><a>Article of the moment archive</a>
  </nav>

  <section class="hero">
    <div class="hero-photo" role="img" aria-label="Advisor standing on a sunny timber boardwalk path lined with trees"></div>
    <div class="slide-arrow prev"><svg width="8" height="11"><path d="M7 0 0 5.5 7 11z" fill="#fff" opacity=".6"/></svg></div>
    <div class="slide-arrow next"><svg width="8" height="11"><path d="M1 0 8 5.5 1 11z" fill="#fff" opacity=".6"/></svg></div>
    <div class="hero-copy">
      <div class="hero-title">Fenway Bridge</div>
      <div class="hero-sub">Advisory</div>
      <div class="hero-tag">Getting to know Fenway Bridge Advisory</div>
    </div>
    <div class="hero-btn">CLIENT LOGIN
      <svg width="12" height="12" viewBox="0 0 12 12"><path d="M1 1l5 5-5 5M6 1l5 5-5 5" fill="none" stroke="#fff" stroke-width="1.5"/></svg>
    </div>
  </section>

  <div class="intro-band"></div>
  <h1 class="welcome">Welcome to Fenway Bridge</h1>
  <p class="intro-text">Fenway Bridge Advisory aims to service the needs of its clients by focusing on the present rather than reporting on historical figures. We recognise that business owners benefit from regular contact with their accountant. One who undertakes a hands on approach in working with business owners to improve their business.</p>

  <h2 class="section" style="left:166px;top:616px">Fenway Bridge Advisory Difference</h2>
  <div class="team-photo" role="img" aria-label="Four team members seated at the reception desk in front of a red wall"></div>
  <div class="diff-text">
    <p>Not all Accountants are created equally … the Fenway Bridge Advisory difference Fenway Bridge Advisory takes pride in not following the status quo, the following points are just some of the unique benefits you will experience when working with us.</p>
    <p>Believing in the here and now: A proactive accountant that focuses on providing timely and relevant information.</p>
  </div>
  <div class="btn" style="left:166px;top:915px;width:102px;height:27px">Read more info</div>

  <h2 class="section" style="left:166px;top:962px">Testimonials</h2>
  <svg class="testi-nav" width="20" height="9" viewBox="0 0 20 9"><path d="M5 1 2 4.5 5 8M15 1l3 3.5L15 8" fill="none" stroke="#999" stroke-width="1.2"/></svg>
  <div class="testimonial" style="left:167px">
    <div class="who">Jo Whitcombe from Brightline Electrical Supplies Pty Ltd</div>
    <div class="quote">We have been using Fenway Bridge Advisory since 2007, and have always found Danielle &amp; her staff to give high quality, effective service.</div>
    <div class="more">[ Read More ]</div>
  </div>
  <div class="testi-divider"></div>
  <div class="testimonial" style="left:381px">
    <div class="who">Jo Whitcombe from Brightline Electrical Supplies Pty Ltd</div>
    <div class="quote">We have been using Fenway Bridge Advisory since 2007, and have always found Danielle &amp; her staff to give high quality, effective service.</div>
    <div class="more">[ Read More ]</div>
  </div>

  <h2 class="section" style="left:587px;top:616px">Articles of the Moment</h2>

  <article class="article" style="top:664px">
    <span class="badge"><svg width="12" height="12" viewBox="0 0 12 12"><path d="M1 1l5 5-5 5M6 1l5 5-5 5" fill="none" stroke="#fff" stroke-width="1.4"/></svg></span>
    <h3>When First Impressions Count...</h3>
    <p class="excerpt">I attended a local solicitors' office this morning and upon arriving was immediately impressed with the appearance of the reception and waiting area. The receptionist greeted me warmly and instructed ...<br>Full story</p>
    <div class="comments"><svg width="10" height="9"><path d="M0 0h10v6H4L1 9V6H0z" fill="#999"/></svg>Comments (3)</div>
    <div class="rule"></div>
  </article>

  <article class="article" style="top:791px">
    <span class="badge"><svg width="12" height="12" viewBox="0 0 12 12"><path d="M1 1l5 5-5 5M6 1l5 5-5 5" fill="none" stroke="#fff" stroke-width="1.4"/></svg></span>
    <h3>6 Tips for Naming your Business</h3>
    <p class="excerpt">I attended a local solicitors' office this morning and upon arriving was immediately impressed with the appearance of the reception and waiting area. The receptionist greeted me warmly and instructed ...<br>Full story</p>
    <div class="comments"><svg width="10" height="9"><path d="M0 0h10v6H4L1 9V6H0z" fill="#999"/></svg>Comments (3)</div>
    <div class="rule"></div>
  </article>

  <article class="article" style="top:918px">
    <span class="badge"><svg width="12" height="12" viewBox="0 0 12 12"><path d="M1 1l5 5-5 5M6 1l5 5-5 5" fill="none" stroke="#fff" stroke-width="1.4"/></svg></span>
    <h3>Energy Efficiency</h3>
    <p class="excerpt">I attended a local solicitors' office this morning and upon arriving was immediately impressed with the appearance of the reception and waiting area. The receptionist greeted me warmly and instructed ...<br>Full story</p>
    <div class="comments"><svg width="10" height="9"><path d="M0 0h10v6H4L1 9V6H0z" fill="#999"/></svg>Comments (3)</div>
  </article>

  <div class="btn" style="left:636px;top:1043px;width:149px;height:27px">View all archived articles</div>

  <footer class="footer">
    <div class="footer-links">Home<span class="sep">|</span>About us<span class="sep">|</span>Services<span class="sep">|</span>Working with us<span class="sep">|</span>Links<span class="sep">|</span>Testimonials<span class="sep">|</span>News<span class="sep">|</span>Article of the moment archive<span class="sep">|</span>Contact us</div>
    <div class="copyright">Copyright © 2013. Fenway Bridge Advisory. All rights reserved.</div>
    <div class="partner"><span class="seal"></span><span class="plate"></span></div>
  </footer>

</div>
</body>
</html>
```